Coastline Premier Retreats Business Card Design

Design a business card for Coastline Premier Retreats. Look at the website for colors and reference. Card should have logo, name, title, office number, mobile number, email, URL and a tagline like, "Luxury Hotel & Resort Email Marketing" (This might change).

https://www.coastlinepremierretreats.example

The rest I will leave up to your imagination.

Contact Information for Business Card

Logo, name, title, office number, mobile number, email, URL and a tagline like, "Luxury Hotel & Resort Email Marketing" (This might change).

```html
<!DOCTYPE html>
<html lang="en">
<head>
<meta charset="utf-8">
<title>Coastline Premier Retreats – Business Card</title>
<link rel="stylesheet" href="https://fonts.googleapis.com/css2?family=Michroma&family=Open+Sans:wght@400;700&display=swap">
<style>
  :root {
    --backdrop: #3b3b3b;
    --card: #1c1c1c;
    --orange: #f07a22;
    --white: #f2f2f2;
    --grey: #b9b9b9;
    --muted: #8a8a8a;
  }
  * { box-sizing: border-box; margin: 0; padding: 0; }
  html, body { width: 1200px; height: 801px; overflow: hidden; }
  body {
    background: radial-gradient(ellipse at 50% 40%, #444 0%, var(--backdrop) 70%);
    font-family: "Open Sans", sans-serif;
    position: relative;
  }
  .card {
    position: absolute;
    top: 246px;
    width: 540px;
    height: 309px;
    background: var(--card);
    border: 1.5px solid var(--orange);
    box-shadow: 0 10px 28px rgba(0,0,0,.45);
    overflow: hidden;
  }
  .card--front { left: 40px; }
  .card--back { left: 620px; }

  .brand {
    position: absolute;
    display: flex;
    align-items: center;
    gap: 12px;
    font-family: "Michroma", sans-serif;
    text-transform: uppercase;
    line-height: 1.35;
  }
  .brand__mark { width: 14px; height: 14px; background: var(--orange); flex: none; }
  .card--front .brand { left: 34px; top: 52px; color: var(--white); font-size: 19px; letter-spacing: 1px; }
  .card--back .brand { left: 40px; top: 78px; color: var(--grey); font-size: 21px; letter-spacing: 1px; }
  .card--back .brand__mark { background: var(--grey); }

  .person { position: absolute; left: 34px; bottom: 46px; }
  .person__name { color: var(--orange); font-weight: 700; font-size: 19px; text-transform: uppercase; letter-spacing: .3px; }
  .person__title { color: var(--grey); font-size: 13px; margin-top: 2px; }

  .divider { position: absolute; left: 236px; top: 150px; width: 1px; height: 90px; background: var(--orange); opacity: .8; }

  .contact { position: absolute; left: 254px; right: 34px; top: 162px; list-style: none; }
  .contact li { display: flex; align-items: center; gap: 8px; color: var(--grey); font-size: 11.5px; line-height: 22px; white-space: nowrap; }
  .contact svg { width: 11px; height: 11px; flex: none; fill: var(--orange); }

  .tagline {
    position: absolute; left: 40px; right: 40px; bottom: 48px;
    font-family: "Michroma", sans-serif; color: var(--white);
    font-size: 10.5px; letter-spacing: 1.8px; text-transform: uppercase; white-space: nowrap;
  }
</style>
</head>
<body>
  <section class="card card--front" aria-label="Card front">
    <div class="brand"><span class="brand__mark"></span><span>Coastline Premier<br>Retreats</span></div>
    <div class="person">
      <p class="person__name">Dorian Vastell</p>
      <p class="person__title">President / CEO</p>
    </div>
    <span class="divider"></span>
    <ul class="contact">
      <li><svg viewBox="0 0 24 24" aria-hidden="true"><path d="M6.6 10.8a15 15 0 0 0 6.6 6.6l2.2-2.2c.3-.3.7-.4 1-.2 1.1.4 2.3.6 3.6.6.6 0 1 .4 1 1V20c0 .6-.4 1-1 1A17 17 0 0 1 3 4c0-.6.4-1 1-1h3.5c.6 0 1 .4 1 1 0 1.3.2 2.5.6 3.6.1.3 0 .7-.2 1z"/></svg>555.214.7300</li>
      <li><svg viewBox="0 0 24 24" aria-hidden="true"><path d="M2 5h20v14H2zm2 2v.5l8 5 8-5V7l-8 5z"/></svg>info@coastlinepremierretreats.example</li>
      <li><svg viewBox="0 0 24 24" aria-hidden="true"><path d="M12 2a10 10 0 1 0 0 20 10 10 0 0 0 0-20zm6.9 6h-3a15 15 0 0 0-1.3-3.9A8 8 0 0 1 18.9 8zM12 4c.8 1.2 1.5 2.5 1.9 4h-3.8c.4-1.5 1.1-2.8 1.9-4zM4.3 14a8 8 0 0 1 0-4h3.4a16 16 0 0 0 0 4zm.8 2h3a15 15 0 0 0 1.300 3.9A8 8 0 0 1 5.1 16zm3-8h-3a8 8 0 0 1 4.3-3.9C8.8 5.3 8.4 6.6 8.1 8zM12 20c-.8-1.2-1.5-2.5-1.9-4h3.8c-.4 1.5-1.1 2.8-1.9 4zm2.3-6H9.7a14 14 0 0 1 0-4h4.6a14 14 0 0 1 0 4zm.3 5.9c.6-1.2 1-2.5 1.3-3.9h3a8 8 0 0 1-4.3 3.9zm1.7-5.9a16 16 0 0 0 0-4h3.4a8 8 0 0 1 0 4z"/></svg>www.coastlinepremierretreats.example</li>
    </ul>
  </section>

  <section class="card card--back" aria-label="Card back">
    <div class="brand"><span class="brand__mark"></span><span>Coastline Premier<br>Retreats</span></div>
    <p class="tagline">Luxury Hotel &amp; Resort Email Marketing</p>
  </section>
</body>
</html>
```